Business Card Design

New business card design

Target Market(s)

Residential & Commercial Property Managers

Industry/Entity Type

Plumbing Services

Contact Information for Business Card

Name - Rowan Keddle, title - Director, Phone Number - 0431 286 517, email - rowan@tbk-plumbing.com.au, Company ABN - 73 215 904 386,

Font styles to use
Sans Serif

Colors
0054AA
0677BA
7BADD7
CADEEF
E8F1F8

```html
<!DOCTYPE html>
<html lang="en">
<head>
<meta charset="utf-8">
<title>TBK Plumbing Services – Business Card</title>
<link href="https://fonts.googleapis.com/css2?family=Montserrat:wght@400;500;700&display=swap" rel="stylesheet">
<style>
  :root {
    --stage: #232323;
    --paper: #ffffff;
    --brand-blue: #2ca8e0;
    --navy: #1c232b;
    --ink: #1e1e1e;
    --edge: #2ca8e0;
  }
  * { box-sizing: border-box; margin: 0; padding: 0; }
  html, body { width: 1200px; height: 780px; overflow: hidden; }
  body {
    background: var(--stage);
    font-family: "Montserrat", Arial, sans-serif;
    position: relative;
  }
  .card {
    position: absolute;
    top: 235px;
    width: 540px;
    height: 310px;
    background: var(--paper);
    border-radius: 18px;
    border-bottom: 4px solid var(--edge);
    overflow: hidden;
  }
  .card--back { left: 30px; }
  .card--front { left: 630px; }

  .wordmark { color: var(--navy); font-weight: 500; line-height: 1; }
  .wordmark__name { display: block; letter-spacing: 2px; }
  .wordmark__tagline { display: block; letter-spacing: 0.6em; }

  .card--back .wordmark {
    position: absolute; left: 0; right: 0; top: 95px; text-align: center;
  }
  .card--back .wordmark__name { font-size: 96px; }
  .card--back .wordmark__tagline { font-size: 15px; margin-top: 14px; }

  .swoosh { position: absolute; inset: 0; width: 540px; height: 306px; }

  .card--front .wordmark {
    position: absolute; right: 32px; top: 30px; text-align: right;
  }
  .card--front .wordmark__name { font-size: 56px; }
  .card--front .wordmark__tagline { font-size: 10px; margin-top: 8px; }

  .contact { position: absolute; left: 150px; bottom: 26px; color: var(--ink); }
  .contact__name { color: var(--brand-blue); font-weight: 700; font-size: 26px; }
  .contact__title { font-size: 16px; margin-top: 2px; }
  .contact__list { list-style: none; margin-top: 16px; font-size: 15px; }
  .contact__item { display: flex; align-items: center; gap: 8px; margin-top: 4px; }
  .contact__icon { width: 14px; height: 14px; fill: var(--brand-blue); }

  .abn {
    position: absolute; right: 28px; bottom: 96px;
    font-size: 14px; color: var(--ink); line-height: 1.35;
  }
</style>
</head>
<body>
  <section class="card card--back" aria-label="Card back">
    <div class="wordmark">
      <span class="wordmark__name">tbk</span>
      <span class="wordmark__tagline">plumbing services</span>
    </div>
  </section>

  <section class="card card--front" aria-label="Card front">
    <svg class="swoosh" viewBox="0 0 540 306" aria-hidden="true">
      <path d="M0 0 H330 C215 60 120 150 98 306 H0 Z" fill="var(--brand-blue)"/>
      <path d="M338 0 C225 60 130 150 104 306 H122 C135 180 220 75 345 0 Z" fill="var(--navy)"/>
    </svg>
    <div class="wordmark">
      <span class="wordmark__name">tbk</span>
      <span class="wordmark__tagline">plumbing services</span>
    </div>
    <div class="contact">
      <p class="contact__name">Rowan Keddle</p>
      <p class="contact__title">Director</p>
      <ul class="contact__list">
        <li class="contact__item">
          <svg class="contact__icon" viewBox="0 0 24 24" aria-hidden="true"><path d="M6.6 10.8a15.1 15.1 0 0 0 6.6 6.6l2.2-2.2a1 1 0 0 1 1-.25 11.4 11.4 0 0 0 3.6.57 1 1 0 0 1 1 1V20a1 1 0 0 1-1 1A17 17 0 0 1 3 4a1 1 0 0 1 1-1h3.5a1 1 0 0 1 1 1c0 1.25.2 2.45.57 3.57a1 1 0 0 1-.25 1z"/></svg>
          0431 286 517
        </li>
        <li class="contact__item">
          <svg class="contact__icon" viewBox="0 0 24 24" aria-hidden="true"><path d="M2 5h20v14H2z M4 7v.5l8 5 8-5V7l-8 5z" fill-rule="evenodd"/></svg>
          rowan@tbk-plumbing.com.au
        </li>
      </ul>
    </div>
    <p class="abn">Company ABN<br>- 73 215 904 386</p>
  </section>
</body>
</html>
```